Oversized Postcard for Estate Planning & Probate 1st 2nd and 3rd prizes

Create a professional, fresh and polished oversized post card for law firm specializing in Estate Planning & Probate Law for High Net Worth Clients

Use any picture(s) of your choice (mine or ones you recommend), logo, headshot and company info

www.morvenashbylaw.com

Westbrook Office - 4800 Kestrel Avenue, Suite 900, Charlotte, NC 28210
Harlowe Office - 13470 Birch Court, Suite 400, Charlotte, NC 28277

Phone (704) 555-0187

Use this card for a Free Consultation

Target Market(s)

young and old families too; business owners

Industry/Entity Type

Law Firm

Font styles to use
Serif
Sans Serif

Requirements
Must have
• Use any picture(s) of your choice (mine or ones you recommend), logo, headshot and company info
• www.morvenashbylaw.com
• Westbrook Office - 4800 Kestrel Avenue, Suite 900, Charlotte, NC 28210
• Harlowe Office - 13470 Birch Court, Suite 400, Charlotte, NC 28277
• Phone (704) 555-0187
• Use this card for a Free Consultation
Nice to have
• great colors and great design; like graphics with depth /shading
Should not have
• don't use too many pics - keep it simple

```html
<!DOCTYPE html>
<html lang="en">
<head>
<meta charset="utf-8">
<title>Morven Ashby Law PLLC – Oversized Postcard</title>
<link rel="stylesheet" href="https://fonts.googleapis.com/css2?family=Open+Sans:ital,wght@0,300;0,400;0,600;1,600&family=Arvo:wght@700&family=Cinzel:wght@400&family=PT+Serif&display=swap">
<style>
  :root {
    --backdrop: #3a3a3c;
    --paper: #ffffff;
    --paper-tint: #eef3f8;
    --teal: #1b7ea6;
    --teal-bright: #1a86b3;
    --navy: #15506f;
    --navy-deep: #124862;
    --office: #186d91;
    --ink: #222;
    --grey-text: #6b6b6b;
    --light-text: #8a8a8a;
    --mail-area: #e4ebf3;
    --rule: #c9d3dc;
  }
  * { box-sizing: border-box; margin: 0; padding: 0; }
  html, body { width: 904px; height: 1200px; overflow: hidden; }
  body { background: var(--backdrop); position: relative; font-family: "Open Sans", sans-serif; }

  .card {
    position: absolute; left: 50px; width: 808px; height: 524px;
    background: var(--paper); overflow: hidden;
    box-shadow: 4px 5px 10px rgba(0,0,0,.55);
  }
  .card--front { top: 60px; background: linear-gradient(180deg, #fff 0%, #f3f7fb 40%, #fff 100%); }
  .card--back { top: 626px; }

  .abs { position: absolute; }

  /* brand */
  .brand-seal { left: 118px; top: 32px; width: 96px; height: 96px; border-radius: 50%;
    background: radial-gradient(circle at 40% 35%, #2a93bd, var(--navy-deep)); border: 3px solid #2b2b2b; }
  .brand-name { font-family: "Open Sans", sans-serif; font-weight: 400; color: var(--teal);
    text-align: center; line-height: 1.15; }
  .brand-name .line-1 { display: block; font-size: 34px; }
  .brand-name .line-2 { display: block; font-size: 17px; letter-spacing: 3px; }

  .front-rule { left: 0; top: 136px; width: 808px; height: 2px; background: #222; }

  .headline { right: 29px; top: 26px; text-align: right; font-family: "Arvo", serif;
    font-weight: 700; font-size: 21px; line-height: 27px; color: var(--teal); }
  .services-line { right: 29px; top: 91px; text-align: right; font-size: 13.6px;
    line-height: 18px; color: var(--grey-text); letter-spacing: .3px; }

  .office { top: 142px; width: 200px; height: 70px; background: var(--office); color: #fff;
    padding: 6px 14px; border-radius: 0 0 5px 5px; }
  .office h3 { font-weight: 600; font-size: 14.5px; margin-bottom: 5px; }
  .office p { font-size: 11.2px; line-height: 14px; }
  .office--west { left: 366px; }
  .office--harlowe { left: 573px; }

  .headshot { left: 30px; top: 258px; width: 169px; height: 210px;
    background: linear-gradient(90deg, #b8b2a6 0%, #d9d4ca 35%, #2b2b2e 70%, #1f2a33 100%); }
  .bio { left: 214px; top: 256px; width: 150px; font-size: 10.6px; line-height: 16.9px;
    font-weight: 300; color: var(--light-text); }

  .family-photo { left: 366px; top: 212px; width: 442px; height: 256px;
    background: linear-gradient(90deg, rgba(240,245,250,0) 0%, #c9d9e2 18%, #9fb8c6 50%, #8aa5b4 80%, #b8c8cf 100%),
                linear-gradient(180deg, #e2ecf2 0%, #b3c7d2 60%, #d6d1c6 100%); }

  .contact-band { left: 0; top: 468px; width: 808px; height: 56px; }
  .band-offer { left: 29px; top: 479px; font-size: 13px; line-height: 17px; color: #e8f3f8; font-weight: 300; }
  .band-offer strong { font-weight: 600; font-style: italic; }
  .band-phone { left: 214px; top: 478px; color: #fff; font-size: 15px; }
  .band-phone .number { font-family: "PT Serif", serif; font-size: 23px; letter-spacing: .5px; }
  .band-web { left: 482px; top: 485px; font-family: "Cinzel", serif; font-size: 18px;
    color: #fff; letter-spacing: 1.6px; }

  /* back */
  .back-brand { left: 30px; top: 40px; width: 262px; }
  .back-brand .rule { height: 2px; background: #222; }
  .back-brand .brand-name { margin: 10px 0 11px; }
  .tagline { left: 60px; top: 144px; width: 200px; text-align: center; font-family: "PT Serif", serif;
    font-size: 5.5px; letter-spacing: .4px; color: var(--teal); }

  .web-block { left: 313px; top: 40px; width: 316px; height: 71px; background: var(--navy-deep);
    text-align: center; padding-top: 9px; }
  .web-block .email { font-size: 17px; font-weight: 300; color: #b9cfdc; letter-spacing: 1.4px; }
  .web-block .site { font-family: "Cinzel", serif; font-size: 16.5px; color: #fff; letter-spacing: 1.4px; margin-top: 5px; }

  .big-phone { left: 333px; top: 122px; font-family: "PT Serif", serif; font-size: 38px; color: var(--teal); letter-spacing: 1px; }

  .postage { left: 678px; top: 12px; width: 117px; height: 116px; background: var(--mail-area);
    display: flex; align-items: center; justify-content: center; text-align: center; font-size: 14px; color: #111; }
  .mail-area { left: 350px; top: 229px; width: 445px; height: 281px; }
  .mail-label { font-size: 14.5px; color: #111; }

  .service-list { left: 345px; top: 245px; width: 161px; list-style: none; text-align: center; }
  .service-list li { font-size: 15.2px; font-weight: 300; color: var(--teal); height: 26.2px; line-height: 25px;
    border-bottom: 1px solid var(--rule); }
  .service-list li:last-child { border-bottom: none; }

  .family-photo--back { left: 0; top: 214px; width: 400px; height: 310px;
    background: radial-gradient(ellipse at 40% 50%, #f0e2d3 0%, #e8d4c2 30%, #d2e3ef 60%, rgba(255,255,255,0) 80%); }
  .back-offer { left: 21px; top: 478px; font-size: 13px; line-height: 18px; color: #8c8c8c; font-weight: 300; }
  .back-offer strong { font-weight: 600; font-style: italic; }
</style>
</head>
<body>

<section class="card card--front" aria-label="Postcard front">
  <div class="abs brand-seal" aria-hidden="true"></div>
  <h2 class="abs headline">Serving clients with compassion<br>and legal guidance is our passion…</h2>
  <p class="abs services-line">Estate Administration, Probate Law, Estate Planning,<br>Wills, Trusts, Living Wills, Healthcare Powers</p>
  <div class="abs front-rule"></div>

  <h1 class="abs brand-name" style="left:28px; top:150px; width:280px;">
    <span class="line-1">Morven Ashby</span><span class="line-2">LAW PLLC</span>
  </h1>

  <div class="abs family-photo" role="img" aria-label="Photo of a smiling multi-generation family walking hand in hand along a beach"></div>

  <div class="abs office office--west">
    <h3>Westbrook Office</h3>
    <p>4800 Kestrel Avenue, Suite 900,<br>Charlotte, NC 28210</p>
  </div>
  <div class="abs office office--harlowe">
    <h3>Harlowe Office</h3>
    <p>13470 Birch Court, Suite 400,<br>Charlotte, NC 28277</p>
  </div>

  <div class="abs headshot" role="img" aria-label="Headshot of the attorney in a dark blazer"></div>
  <p class="abs bio">Morven Ashby Law, PLLC serving clients in estate planning, estate administration, probate law, wills, revocable trusts, irrevocable trusts, powers of attorney, health care powers of attorney, living wills, hipaa releases, guardianships, special needs planning, wealth transfers, elder law and business law in North Carolina and South Carolina.</p>

  <svg class="abs contact-band" width="808" height="56" viewBox="0 0 808 56" aria-hidden="true">
    <rect width="808" height="56" fill="var(--navy)"/>
    <polygon points="0,0 215,0 190,56 0,56" fill="var(--teal-bright)"/>
    <polygon points="462,0 808,0 808,56 418,56" fill="var(--navy-deep)"/>
  </svg>
  <p class="abs band-offer">Use this card for a<br><strong>Free Consultation</strong></p>
  <p class="abs band-phone">Phone: <span class="number">(704) 555-0187</span></p>
  <p class="abs band-web">WWW.MORVENASHBYLAW.COM</p>
</section>

<section class="card card--back" aria-label="Postcard back">
  <div class="abs back-brand">
    <div class="rule"></div>
    <h1 class="brand-name"><span class="line-1">Morven Ashby</span><span class="line-2">LAW PLLC</span></h1>
    <div class="rule"></div>
  </div>
  <p class="abs tagline">PLANNING TODAY FOR YOUR TOMORROW</p>

  <div class="abs web-block">
    <p class="email">morven@morvenashbylaw.com</p>
    <p class="site">WWW.MORVENASHBYLAW.COM</p>
  </div>
  <p class="abs big-phone">(704) 555-0187</p>

  <div class="abs postage">Postage<br>Area</div>

  <svg class="abs mail-area" width="445" height="281" viewBox="0 0 445 281" aria-hidden="true">
    <polygon points="188,0 445,0 445,281 0,281 0,221 188,221" fill="var(--mail-area)"/>
  </svg>
  <p class="abs mail-label" style="left:620px; top:241px;">Address Area</p>
  <p class="abs mail-label" style="left:530px; top:479px;">Barcode Area</p>

  <div class="abs family-photo--back" role="img" aria-label="Photo of a grandmother, mother and young daughter hugging and laughing by the sea"></div>

  <ul class="abs service-list">
    <li>Estate Administration</li>
    <li>Probate Law</li>
    <li>Estate Planning</li>
    <li>Wills</li>
    <li>Trusts</li>
    <li>Living Wills</li>
    <li>Healthcare Powers</li>
  </ul>

  <p class="abs back-offer">Use this card for a<br><strong>Free Consultation</strong></p>
</section>

</body>
</html>
```